Onsite Energy for Retail Tenants

Need a short one page-3 part build showing how the program for discounted clean energy works - moving into a call to action with multiple links.

1) Solar Garden Produces Energy
2) Credits Available for Tenants’ Utility Bills
3) Sign Up to Receive Utility Bill Credits.
Save 5%

This document will be used:
1) Embedded in Mailchimp emails
2) as an html landing page
3) as an image

Use the latest powerpoint Tenant slide E as guidance
Updates

Infographic is simplistic. 3 part build using graphics and information. Flow is really important so Gifs welcome.

Target Market(s)

Owners of small stores throughout the US.

Industry/Entity Type

Real Estate

Colors

Designer to choose colors to be used in the design.

Requirements
Must have
• It must explain the program clearly and succinctly using the language from the first slide of Mockup 1. This slide must become an elegant build for the 3 step process. See Mockup 2 for its cleanliness ideas for a similar but different program.
• The second slide of mockup 1 is the call to action and must have clickable links and promote trust.
• Please use the attached font styles.
• The text is sparse and so needs to be bold and in order and with the graphics needs to explain how it works perfectly.
• The graphics should be clean and sophisticated but the message and flow needs to be simple.
Nice to have
• Moving arrows to show flow of energy and credits.
• Ability to switch out language of text.

```html
<!DOCTYPE html>
<html lang="en">
<head>
<meta charset="utf-8">
<title>How Clean Discount Electricity Works</title>
<link href="https://fonts.googleapis.com/css2?family=Roboto+Condensed:wght@300;400&display=swap" rel="stylesheet">
<style>
  :root {
    --ink: #0e1319;
    --bg: #eefcfd;
    --blue: #3b8ff0;
    --deep-blue: #1a3ee8;
    --sky: #4dcdf5;
    --panel: #c4f7fb;
    --soft-cyan: #7ee2f4;
    --white: #ffffff;
    --leader: #8fa3b3;
  }
  * { margin: 0; padding: 0; box-sizing: border-box; }
  html, body { width: 928px; height: 1200px; overflow: hidden; }
  body {
    position: relative;
    background: radial-gradient(circle at 60% 40%, #f6ffff 0%, var(--bg) 70%);
    font-family: "Roboto Condensed", sans-serif;
    font-weight: 300;
    color: var(--ink);
  }
  .abs { position: absolute; }
  .corner-wedge { left: 0; top: 0; }
  .title-bar { left: 79px; top: 37px; }
  .title-text {
    left: 141px; top: 41px;
    font-size: 37px; font-weight: 400; color: var(--white);
    letter-spacing: -0.2px; white-space: nowrap;
  }
  .step-label { display: flex; gap: 8px; font-size: 20px; line-height: 1.3; white-space: nowrap; }
  .step-label .num { font-size: 36px; line-height: 1; color: var(--blue); }
  .step-one { left: 145px; top: 155px; }
  .step-two { left: 731px; top: 176px; }
  .step-three { left: 102px; top: 376px; }
  .save-big {
    left: 126px; top: 448px;
    font-size: 52px; font-weight: 400; color: var(--deep-blue); white-space: nowrap;
  }
  .leaders { left: 0; top: 0; }
  .scene { left: 280px; top: 110px; }
  .offer-panel {
    left: 60px; top: 660px; width: 808px; height: 414px;
    background: var(--panel);
  }
  .offer-title {
    position: absolute; top: 8px; width: 100%; text-align: center;
    font-size: 44px; font-weight: 400; color: var(--blue); white-space: nowrap;
  }
  .offer-sub {
    position: absolute; top: 60px; width: 100%; text-align: center;
    font-size: 25px; color: var(--soft-cyan); white-space: nowrap;
  }
  .card {
    position: absolute; top: 93px; width: 254px; height: 228px;
    background: var(--white); border-radius: 16px; overflow: hidden;
    text-align: center;
  }
  .card-one { left: 100px; }
  .card-two { left: 454px; }
  .card-head {
    height: 43px; background: var(--sky);
    display: flex; align-items: center; justify-content: center; gap: 10px;
    color: var(--white); font-size: 26px; font-weight: 400;
  }
  .card-head .divider { width: 1px; height: 26px; background: var(--white); }
  .card-lead { margin-top: 14px; font-size: 18.5px; line-height: 1.3; white-space: nowrap; }
  .card-note { margin-top: 24px; font-size: 15px; line-height: 1.35; white-space: nowrap; }
  .cta-bar {
    position: absolute; left: 0; top: 339px; width: 808px; height: 50px;
    background: var(--ink);
  }
  .cta-button {
    position: absolute; top: 9px; height: 31px;
    background: var(--blue); color: var(--white);
    font-family: "Roboto Condensed", sans-serif;
    font-size: 15px; white-space: nowrap;
    display: flex; align-items: center; justify-content: center;
    text-decoration: none; border-radius: 2px;
  }
  .cta-learn { left: 211px; width: 145px; font-weight: 400; }
  .cta-contact { left: 452px; width: 146px; font-weight: 300; }
  .brand {
    left: 0; top: 1104px; width: 928px; text-align: center;
    font-size: 33px; font-weight: 400; color: var(--blue); letter-spacing: 1.5px;
  }
</style>
</head>
<body>
  <svg class="abs corner-wedge" width="120" height="330" viewBox="0 0 120 330">
    <polygon points="0,0 112,0 0,323" fill="var(--blue)"/>
  </svg>

  <svg class="abs title-bar" width="692" height="64" viewBox="0 0 692 64">
    <polygon points="0,0 640,0 672,32 640,64 0,64" fill="var(--ink)"/>
    <polygon points="640,0 687,0 687,14 672,32" fill="var(--soft-cyan)"/>
    <polygon points="672,32 687,14 687,64 640,64" fill="var(--blue)"/>
  </svg>
  <h1 class="abs title-text">How Clean Discount Electricity Works?</h1>

  <svg class="abs leaders" width="928" height="560" viewBox="0 0 928 560">
    <g stroke="var(--leader)" stroke-width="1" stroke-dasharray="2 2" fill="none">
      <polyline points="153,195 153,292 285,292"/>
      <polyline points="740,225 740,451 712,451"/>
      <polyline points="110,420 110,535 300,535"/>
    </g>
  </svg>

  <svg class="abs scene" width="440" height="500" viewBox="0 0 440 500" role="img" aria-label="Illustration of a sun shining on a solar panel, power poles carrying energy to a battery, and a house receiving clean energy, all inside a circular landscape">
    <defs>
      <linearGradient id="sceneFill" x1="0" y1="0" x2="0" y2="1">
        <stop offset="0" stop-color="#c9fbf4"/>
        <stop offset="0.5" stop-color="#5cc6f5"/>
        <stop offset="1" stop-color="#3e8cf0"/>
      </linearGradient>
    </defs>
    <circle cx="221" cy="254" r="207" fill="url(#sceneFill)"/>
  </svg>

  <div class="abs step-label step-one"><span class="num">1</span><span>Solar Garden Produces<br>Energy and Property<br>receives Utility Credits</span></div>
  <div class="abs step-label step-two"><span class="num">2</span><span>Credits Available<br>for Tenants’<br>Utility Bills</span></div>
  <div class="abs step-label step-three"><span class="num">3</span><span>Sign Up to Receive<br>Credits on your<br>Utility Bill</span></div>
  <div class="abs save-big">Save 5%</div>

  <section class="abs offer-panel">
    <h2 class="offer-title">ELECTRICITY DISCOUNT OFFER</h2>
    <p class="offer-sub">Save 5% on your Electricity Cost</p>

    <article class="card card-one">
      <div class="card-head">
        <svg width="22" height="24" viewBox="0 0 22 24" aria-hidden="true"><path d="M2 1h12l5 5v17H2z" fill="none" stroke="var(--white)" stroke-width="1.6"/><path d="M6 11l2 2 4-4M6 17h9" stroke="var(--white)" stroke-width="1.6" fill="none"/></svg>
        <span class="divider"></span>Step 1</div>
      <p class="card-lead">Sign Up for the<br>Electricity Discount<br>Agreement.</p>
      <p class="card-note">It runs only for<br>as long as you lease.<br>Your Discount is Guaranteed</p>
    </article>

    <article class="card card-two">
      <div class="card-head">
        <svg width="22" height="24" viewBox="0 0 22 24" aria-hidden="true"><path d="M2 1h12l5 5v17H2z" fill="none" stroke="var(--white)" stroke-width="1.6"/><path d="M6 11l2 2 4-4M6 17h9" stroke="var(--white)" stroke-width="1.6" fill="none"/></svg>
        <span class="divider"></span>Step 2</div>
      <p class="card-lead">Securely Provide Sunfield Solar<br>with your Utility information<br>through GridLink</p>
      <p class="card-note">We use the information only to credit<br>your bill, generate your invoice, and<br>provide clean discounted energy.</p>
    </article>

    <div class="cta-bar">
      <a class="cta-button cta-learn" href="#learn-more">Click here to learn more</a>
      <a class="cta-button cta-contact" href="#contact">Contact Us</a>
    </div>
  </section>

  <div class="abs brand">GRIDLINK</div>
</body>
</html>
```